Business Card for a Dental Office

The design should communicate integrity, quality and reliability. We also want the card look elegant, simple, but still stand out, different from the traditional-dental-office business card.

Industry/Entity Type

Business

```html
<!DOCTYPE html>
<html lang="en">
<head>
<meta charset="utf-8">
<title>Harlow Dental Centre – Business Card</title>
<link href="https://fonts.googleapis.com/css2?family=Bebas+Neue&family=Source+Sans+3:wght@400;600&display=swap" rel="stylesheet">
<style>
  :root {
    --stage: #000000;
    --card-light: #f4f4f4;
    --card-white: #ffffff;
    --ink: #111111;
    --gold: #c9a916;
    --gold-deep: #b59d18;
    --gold-bright: #cdb424;
    --on-gold: #ffffff;
  }
  * { margin: 0; padding: 0; box-sizing: border-box; }
  html, body {
    width: 1200px; height: 900px; overflow: hidden;
    background: var(--stage);
  }
  .canvas { position: relative; width: 1200px; height: 900px; }

  .card {
    position: absolute; top: 200px; width: 310px; height: 502px;
    overflow: hidden;
  }
  .card--front {
    left: 265px;
    background: linear-gradient(180deg, var(--card-white) 0%, var(--card-light) 40%, var(--card-light) 100%);
    border-radius: 62px 0 62px 0;
  }
  .card--back {
    left: 641px;
    background: linear-gradient(160deg, var(--gold-bright) 0%, var(--gold) 45%, var(--gold-deep) 100%);
    border-radius: 0 62px 0 62px;
  }

  .brand-mark {
    position: absolute; left: 127px; top: 52px;
    width: 56px; height: 56px; background: var(--gold);
  }
  .brand-name {
    position: absolute; left: 0; width: 100%; text-align: center;
    font-family: "Bebas Neue", "Arial Narrow", sans-serif;
    font-size: 34px; line-height: 1; letter-spacing: 0.2px;
    color: var(--ink);
  }
  .card--front .brand-name { top: 148px; }
  .brand-tagline {
    position: absolute; left: 0; width: 100%; text-align: center;
    font-family: "Source Sans 3", "Myriad Pro", sans-serif;
    font-weight: 600; font-size: 13.5px; letter-spacing: 1px;
    color: var(--gold); white-space: nowrap;
  }
  .card--front .brand-tagline { top: 175px; }

  .card--back .brand-name { top: 411px; color: var(--on-gold); }
  .card--back .brand-tagline { top: 439px; color: var(--on-gold); }

  .contact {
    position: absolute; left: 27px; top: 326px;
    font-family: "Source Sans 3", "Myriad Pro", sans-serif;
    color: var(--ink);
  }
  .contact__name {
    font-weight: 600; font-size: 18px; color: var(--gold);
    letter-spacing: 0.2px; line-height: 22px;
  }
  .contact__role { font-size: 14.5px; line-height: 20px; }
  .contact__address { margin-top: 19px; font-size: 14px; line-height: 16px; }
  .contact__line {
    display: flex; align-items: center; gap: 6px;
    font-size: 14px; line-height: 19px;
  }
  .contact__line--phone { margin-top: 11px; }
  .contact__line svg { width: 10px; height: 10px; }
</style>
</head>
<body>
<main class="canvas">
  <section class="card card--front" aria-label="Card front">
    <div class="brand-mark"></div>
    <div class="brand-name">Harlow Dental Centre</div>
    <div class="brand-tagline">CARING HANDS FOR A BRIGHTER SMILE</div>

    <div class="contact">
      <div class="contact__name">ELLA MARSH</div>
      <div class="contact__role">Managing Director</div>
      <div class="contact__address">58 Harbour Lane, Suite 2<br>Northvale, NV 40217</div>
      <div class="contact__line contact__line--phone">
        <svg viewBox="0 0 10 10" aria-hidden="true"><path fill="var(--gold)" d="M1 3.2C1 1.8 2.8 1 5 1s4 .8 4 2.2V4H7V3H3v1H1z M2 5.2L3.4 3.6h3.2L8 5.2V9H2z"/></svg>
        <span>555-214-3098</span>
      </div>
      <div class="contact__line">
        <svg viewBox="0 0 10 10" aria-hidden="true"><rect x="0.5" y="2" width="9" height="6" fill="var(--gold)"/><path d="M0.8 2.3L5 5.4 9.2 2.3" fill="none" stroke="#fff" stroke-width=".7"/></svg>
        <span>hello@harlowdental.com</span>
      </div>
    </div>
  </section>

  <section class="card card--back" aria-label="Card back">
    <div class="brand-name">Harlow Dental Centre</div>
    <div class="brand-tagline">CARING HANDS FOR A BRIGHTER SMILE</div>
  </section>
</main>
</body>
</html>
```